Drifting Lantern Coffee Co menu

We would like our existing menu tidied up.
we want to keep the all the items, but need it less busy and clearer to read.

Also want to leave a bit of space to add a few item in the future.

```html
<!DOCTYPE html>
<html lang="en">
<head>
<meta charset="utf-8">
<title>Drifting Lantern Coffee Co — Iced Coffee &amp; Milkshakes Menu</title>
<link rel="stylesheet" href="https://fonts.googleapis.com/css2?family=Sancreek&family=Marcellus&family=Arimo:wght@400;700&display=swap">
<style>
  :root {
    --ink: #0d0d0d;
    --paper: #ffffff;
    --watermark: #e9e9e9;
  }
  * { margin: 0; padding: 0; box-sizing: border-box; }
  html, body { width: 777px; height: 1200px; overflow: hidden; background: var(--paper); }
  .menu {
    position: relative; width: 777px; height: 1200px; overflow: hidden;
    background: var(--paper); color: var(--ink);
    font-family: "Arimo", Arial, sans-serif;
  }
  .menu > * { position: absolute; }
  .watermark {
    left: 35px; top: 150px; width: 712px; height: 760px;
    background: radial-gradient(ellipse at 55% 50%, var(--watermark) 0%, rgba(233,233,233,0.7) 45%, rgba(233,233,233,0) 72%);
  }
  .title {
    left: 0; width: 777px; top: 30px; text-align: center;
    font-family: "Sancreek", serif; font-size: 78px; line-height: 90px; letter-spacing: 1px;
  }
  .subtitle {
    left: 0; width: 777px; top: 112px; text-align: center;
    font-family: "Marcellus", serif; font-size: 38px; line-height: 40px;
  }
  .subtitle-rule { left: 240px; top: 152px; width: 282px; height: 2px; background: var(--ink); border-radius: 2px; }
  .rule { height: 3px; background: var(--ink); }
  .section-head {
    font-size: 18px; font-weight: 700; line-height: 22px;
    text-decoration: underline; text-underline-offset: 3px; text-decoration-thickness: 1.5px;
  }
  .item { font-size: 19px; font-weight: 700; line-height: 22px; }
  .price { font-size: 12px; font-weight: 700; line-height: 22px; text-align: right; width: 60px; }
  .note { font-size: 11.5px; line-height: 16px; }
  .left-price { left: 292px; }
  .right-price { left: 676px; }
  .specialty-title {
    left: 0; width: 777px; top: 590px; text-align: center;
    font-family: "Sancreek", serif; font-size: 46px; line-height: 56px;
  }
  .special-name, .special-desc, .special-price { left: 0; width: 777px; text-align: center; }
  .special-name { font-size: 19px; font-weight: 700; line-height: 22px; }
  .special-desc { font-size: 11.6px; line-height: 17.4px; }
  .special-price { font-size: 12px; font-weight: 700; line-height: 16px; }
</style>
</head>
<body>
<main class="menu">
  <div class="watermark" role="img" aria-label="Faint leaf emblem in the background"></div>

  <h1 class="title">ICED COFFEE</h1>
  <p class="subtitle">&amp; Milkshakes</p>
  <div class="subtitle-rule"></div>

  <!-- Iced coffee column -->
  <div class="rule" style="left:43px;top:179px;width:309px"></div>
  <h2 class="section-head" style="left:43px;top:197px">Iced Coffee&nbsp;&nbsp;</h2>
  <p class="item" style="left:43px;top:234px">Iced Latte</p>
  <p class="price left-price" style="top:234px">$7.50</p>
  <p class="note" style="left:44px;top:264px">Add Icecream + $1.00</p>
  <p class="item" style="left:43px;top:290px">Iced Mocha</p>
  <p class="price left-price" style="top:290px">$8.00</p>
  <p class="note" style="left:44px;top:320px">Add Icecream + $1.00</p>
  <p class="item" style="left:43px;top:346px">Iced Americano</p>
  <p class="price left-price" style="top:346px">$6.00</p>
  <p class="item" style="left:43px;top:378px">Cold Brew</p>
  <p class="price left-price" style="top:378px">$7.50</p>

  <div class="rule" style="left:43px;top:414px;width:309px"></div>
  <h2 class="section-head" style="left:43px;top:430px">Other Drinks&nbsp;</h2>
  <p class="item" style="left:43px;top:467px">Iced Chocolate</p>
  <p class="price left-price" style="top:467px">$7.00</p>
  <p class="item" style="left:43px;top:497px">Iced Chai</p>
  <p class="price left-price" style="top:497px">$7.00</p>
  <p class="item" style="left:43px;top:529px">Puppycino</p>
  <p class="price left-price" style="top:531px">$2.00</p>

  <!-- Milkshake column -->
  <div class="rule" style="left:428px;top:179px;width:308px"></div>
  <h2 class="section-head" style="left:427px;top:197px">Milkshakes&nbsp;&nbsp;</h2>
  <p class="note" style="left:427px;top:223px">Milkshake with a choice of chilled milk and ice cream.</p>
  <p class="item" style="left:427px;top:250px">Chocolate</p>
  <p class="price right-price" style="top:250px">$8.00</p>
  <p class="item" style="left:427px;top:285px">Vanilla</p>
  <p class="price right-price" style="top:285px">$8.00</p>
  <p class="item" style="left:427px;top:321px">Caramel</p>
  <p class="price right-price" style="top:321px">$8.00</p>
  <p class="item" style="left:427px;top:359px">Strawberry</p>
  <p class="price right-price" style="top:359px">$8.00</p>
  <p class="item" style="left:427px;top:395px">Mango</p>
  <p class="price right-price" style="top:395px">$8.00</p>
  <p class="item" style="left:427px;top:431px">Banana</p>
  <p class="price right-price" style="top:431px">$8.00</p>
  <p class="item" style="left:427px;top:467px">Cookies &amp; Cream</p>
  <p class="price right-price" style="top:467px">$8.00</p>
  <p class="item" style="left:427px;top:502px">Hazelnova Milkshake</p>
  <p class="price right-price" style="top:502px">$9.00</p>

  <div class="rule" style="left:43px;top:568px;width:693px"></div>

  <!-- Specialty drinks -->
  <h2 class="specialty-title">SPECIALTY DRINKS</h2>

  <h3 class="special-name" style="top:665px">Crumbleton Iced Coffee</h3>
  <p class="special-desc" style="top:693px">A Double Shot Of Espresso Extracted Over Crumbleton Spread<br>Poured Over Meadowvale Premium Extra Creamy Milk And Ice Cream<br>Topped Off With Whipped Cream And Crushed Crumbleton Cookies</p>
  <p class="special-price" style="top:756px">$9.00</p>

  <h3 class="special-name" style="top:784px">Maltbite Iced Coffee</h3>
  <p class="special-desc" style="top:813px">A Double Shot Of Espresso Extracted Over Melted Maltbites<br>Poured Over Meadowvale Premium Extra Creamy Milk And Ice Cream<br>Topped Off With Whipped Cream And More Crushed Maltbites</p>
  <p class="special-price" style="top:875px">$9.00</p>

  <h3 class="special-name" style="top:903px">Hazelnova Iced Coffee</h3>
  <p class="special-desc" style="top:931px">A Double Shot Of Espresso Extracted Over Melted Hazelnova<br>Poured Over Meadowvale Premium Extra Creamy Milk And Ice Cream<br>Topped Off With Whipped Cream And More Hazelnova Sauce And Crushed Hazelnuts</p>
  <p class="special-price" style="top:993px">$9.00</p>

  <h3 class="special-name" style="top:1020px">Colombian Cacoa Salted Caramel Milkshake</h3>
  <p class="special-desc" style="top:1049px">Colombian Cacoa Salted Caramel Milkshake<br>Made With Deep Toned And Rich Cocoa Sourced From Ancient Cocao Growing Regions Of Colombia And Sweetened<br>With Just Enough Organic Unrefined Colombian Panela, All Balanced Perfectly With A Caramel Raw Natural Infusion<br>And Pink Himalayan Rock Salt. All Blended Together With Icecream And A Choice Of Milk</p>
  <p class="special-price" style="top:1129px">$9.00</p>

  <div class="rule" style="left:43px;top:1160px;width:693px"></div>
</main>
</body>
</html>
```